Small Business Broker Business Card Design

A business card design for a small business brokerage, which is a financial service, not unlike real estate brokerage, but for small businesses such as laundromats, pizza shops, restaurants, cleaners etc. The designs should all be simple, more conservative in nature, using the colors and font of the logo. Again, think real estate Brokerage as a business context
Contact Information for Business Card
Name: Glen R. Harlow. Title: Small Business Advisor. Email: g.harlow@bayfieldcapitalworks.example. Mobile: (555) 274-3918. Office: (555) 806-2147. www.bayfieldcapitalworks.example

```html
<!DOCTYPE html>
<html lang="en">
<head>
<meta charset="utf-8">
<title>Bayfield Capital Works – Business Card</title>
<link rel="stylesheet" href="https://fonts.googleapis.com/css2?family=Open+Sans:wght@400;600;700&display=swap">
<style>
  :root {
    --stage: #222222;
    --green: #8dc63f;
    --green-deep: #6fa52a;
    --navy: #173a6b;
    --ink: #1a1a1a;
    --paper: #ffffff;
  }
  * { margin: 0; padding: 0; box-sizing: border-box; }
  html, body { width: 1200px; height: 780px; overflow: hidden; }
  body {
    background: var(--stage);
    font-family: "Open Sans", Arial, sans-serif;
    display: flex; align-items: center; justify-content: center; gap: 40px;
  }
  .card {
    position: relative;
    width: 540px; height: 308px;
    border-radius: 22px;
    overflow: hidden;
  }
  .card-front { background: var(--paper); }
  .card-shapes { position: absolute; inset: 0; }
  .brand {
    position: absolute; left: 34px; top: 92px; width: 190px;
    display: flex; align-items: center; gap: 10px;
  }
  .brand-mark { width: 16px; height: 16px; background: var(--green); flex: none; }
  .brand-name {
    color: var(--navy); font-weight: 700; font-size: 15px; line-height: 1.25;
    text-transform: uppercase; letter-spacing: .5px;
  }
  .divider {
    position: absolute; left: 244px; top: 64px; width: 1.5px; height: 150px;
    background: var(--ink);
  }
  .person { position: absolute; left: 264px; top: 56px; }
  .person-name { font-size: 26px; font-weight: 700; line-height: 1.1; }
  .person-name .first { color: var(--green); }
  .person-name .last { color: var(--navy); }
  .person-title { font-size: 14px; color: var(--ink); margin-top: 4px; font-weight: 600; }
  .contact-list { list-style: none; margin-top: 10px; }
  .contact-list li {
    display: flex; align-items: center; gap: 8px;
    font-size: 12.5px; color: var(--ink); line-height: 1.6;
    white-space: nowrap;
  }
  .contact-list svg { width: 12px; height: 12px; flex: none; }
  .address {
    position: absolute; left: 34px; top: 228px;
    font-size: 14px; color: var(--ink);
  }
  .card-back { background: var(--green); display: flex; align-items: center; justify-content: center; }
  .back-brand { display: flex; align-items: center; gap: 14px; }
  .back-brand .brand-mark { width: 24px; height: 24px; background: var(--green-deep); }
  .back-brand .brand-name { color: var(--green-deep); font-size: 24px; }
</style>
</head>
<body>
  <section class="card card-front">
    <svg class="card-shapes" viewBox="0 0 540 308" aria-hidden="true">
      <path d="M0 0 H250 C150 10 60 50 0 110 Z" fill="var(--green)"/>
      <path d="M540 222 C480 268 410 295 340 308 H540 Z" fill="var(--navy)"/>
    </svg>
    <div class="brand">
      <span class="brand-mark"></span>
      <span class="brand-name">Bayfield Capital Works, Inc</span>
    </div>
    <div class="divider"></div>
    <div class="person">
      <h1 class="person-name"><span class="first">Glen</span> <span class="last">R. Harlow</span></h1>
      <p class="person-title">Small Business Advisor</p>
      <ul class="contact-list">
        <li>
          <svg viewBox="0 0 24 24"><path fill="var(--green)" d="M6.6 10.8a15 15 0 0 0 6.6 6.6l2.2-2.2a1 1 0 0 1 1-.25 11.4 11.4 0 0 0 3.6.57 1 1 0 0 1 1 1V20a1 1 0 0 1-1 1A17 17 0 0 1 3 4a1 1 0 0 1 1-1h3.5a1 1 0 0 1 1 1c0 1.25.2 2.45.57 3.57a1 1 0 0 1-.25 1z"/></svg>
          M: (555) 274-3918
        </li>
        <li>
          <svg viewBox="0 0 24 24"><path fill="var(--green)" d="M6.6 10.8a15 15 0 0 0 6.6 6.6l2.2-2.2a1 1 0 0 1 1-.25 11.4 11.4 0 0 0 3.6.57 1 1 0 0 1 1 1V20a1 1 0 0 1-1 1A17 17 0 0 1 3 4a1 1 0 0 1 1-1h3.5a1 1 0 0 1 1 1c0 1.25.2 2.45.57 3.57a1 1 0 0 1-.25 1z"/></svg>
          O: (555) 806-2147
        </li>
        <li>
          <svg viewBox="0 0 24 24"><rect x="2" y="5" width="20" height="14" rx="2" fill="var(--green)"/><path d="M3 6l9 7 9-7" stroke="#fff" stroke-width="2" fill="none"/></svg>
          g.harlow@bayfieldcapitalworks.example
        </li>
        <li>
          <svg viewBox="0 0 24 24"><circle cx="12" cy="12" r="10" fill="var(--green)"/><path d="M2 12h20M12 2c3 3 3 17 0 20M12 2c-3 3-3 17 0 20" stroke="#fff" stroke-width="1.5" fill="none"/></svg>
          www.bayfieldcapitalworks.example
        </li>
      </ul>
    </div>
    <p class="address">1840 Harbor Crest Ave. Suite 310 Fairview, TX 75069</p>
  </section>

  <section class="card card-back">
    <div class="back-brand">
      <span class="brand-mark"></span>
      <span class="brand-name">Bayfield Capital Works, Inc</span>
    </div>
  </section>
</body>
</html>
```